iPhone iOS 7 App For Managing Tasks/Photos for Internal Company Use

We need an app design that displays company objectives and task, and provides the interface for employees to complete a task by uploading a photo and adding comments.

Please see attached mock up sketches as a rough guideline

Final delivery of files must contain PSD, and all layers/objects sliced both is PSD and PNG files

Target Market(s)

This is a tool for internal employee use

Industry/Entity Type

It Company

Requirements
Must have
• Must include logo, and match the colour scheme
Use iPhone iOS 7 Style

```html
<!DOCTYPE html>
<html lang="en">
<head>
<meta charset="utf-8">
<title>Objectives – Task App Screen</title>
<link href="https://fonts.googleapis.com/css2?family=Roboto:wght@300;400;500&display=swap" rel="stylesheet">
<style>
  :root {
    --canvas-bg: #262626;
    --screen-bg: #ffffff;
    --nav-top: #4f7b9d;
    --nav-bottom: #7ea7c1;
    --nav-text: #ffffff;
    --body-text: #1a1a1a;
    --divider: #d9d9d9;
    --chevron: #9a9a9a;
    --progress-track: #e2e2e2;
    --progress-fill: #416b93;
    --tab-bg: #f8f8f8;
    --tab-text: #555555;
    --tab-active: #2f5f8f;
  }
  * { box-sizing: border-box; margin: 0; padding: 0; }
  html, body {
    width: 1200px; height: 865px; overflow: hidden;
    background: var(--canvas-bg);
    font-family: "Roboto", "Helvetica Neue", Arial, sans-serif;
  }
  .screen {
    position: absolute; left: 375px; top: 32px;
    width: 450px; height: 800px;
    background: var(--screen-bg);
    display: flex; flex-direction: column;
    overflow: hidden;
  }
  .header {
    background: linear-gradient(100deg, var(--nav-top), var(--nav-bottom));
    color: var(--nav-text);
    height: 112px;
  }
  .status-bar {
    height: 30px; display: flex; align-items: center; justify-content: space-between;
    padding: 0 12px; font-size: 13px;
  }
  .carrier { display: flex; align-items: center; gap: 5px; }
  .signal { display: flex; gap: 2px; }
  .signal span { width: 7px; height: 7px; border-radius: 50%; border: 1px solid var(--nav-text); }
  .signal span.on { background: var(--nav-text); }
  .battery { display: flex; align-items: center; gap: 6px; }
  .battery-icon { width: 26px; height: 12px; border: 1px solid var(--nav-text); border-radius: 3px; padding: 1px; position: relative; }
  .battery-icon::before { content: ""; display: block; width: 50%; height: 100%; background: var(--nav-text); border-radius: 1px; }
  .battery-icon::after { content: ""; position: absolute; right: -4px; top: 3px; width: 2px; height: 4px; background: var(--nav-text); }
  .nav-bar { position: relative; height: 82px; display: flex; align-items: center; justify-content: center; }
  .back-button { position: absolute; left: 12px; display: flex; align-items: center; gap: 6px; font-size: 22px; font-weight: 300; }
  .nav-title { font-size: 32px; font-weight: 300; letter-spacing: 0.5px; }
  .content { flex: 1; padding: 0 0 0 18px; }
  .section-title { font-size: 24px; font-weight: 400; color: var(--body-text); padding: 18px 0 6px; }
  .objective {
    display: flex; justify-content: space-between; align-items: center;
    height: 98px; border-bottom: 1px solid var(--divider); padding-right: 16px;
  }
  .objective-text { font-size: 20px; line-height: 25px; color: var(--body-text); width: 268px; }
  .objective-meta { width: 118px; display: flex; flex-direction: column; align-items: flex-end; gap: 4px; }
  .progress-label { font-size: 10px; font-weight: 500; color: var(--body-text); align-self: flex-start; margin-left: 8px; }
  .progress { width: 118px; height: 10px; background: var(--progress-track); }
  .progress-fill { width: 60%; height: 100%; background: var(--progress-fill); }
  .tab-bar {
    height: 96px; background: var(--tab-bg); border-top: 1px solid var(--divider);
    display: flex; justify-content: space-around; align-items: center;
  }
  .tab { display: flex; flex-direction: column; align-items: center; gap: 4px; font-size: 14px; color: var(--tab-text); width: 100px; }
  .tab.active { color: var(--tab-active); }
  .tab svg { width: 34px; height: 34px; }
</style>
</head>
<body>
<main class="screen">
  <header class="header">
    <div class="status-bar">
      <div class="carrier">
        <div class="signal"><span class="on"></span><span class="on"></span><span></span><span></span><span></span></div>
        <span>NTW</span>
        <svg width="14" height="11" viewBox="0 0 14 11" fill="none" stroke="#fff" stroke-width="1.4"><path d="M1 4a9 9 0 0 1 12 0M3.2 6.3a6 6 0 0 1 7.6 0M5.4 8.5a2.6 2.6 0 0 1 3.2 0"/></svg>
      </div>
      <div class="time">5:17 PM</div>
      <div class="battery"><span>50 %</span><div class="battery-icon"></div></div>
    </div>
    <div class="nav-bar">
      <div class="back-button">
        <svg width="12" height="20" viewBox="0 0 12 20" fill="none" stroke="#fff" stroke-width="2.5"><path d="M10 2 2 10l8 8"/></svg>
        <span>Back</span>
      </div>
      <h1 class="nav-title">Objectives</h1>
    </div>
  </header>

  <section class="content">
    <h2 class="section-title">Select An Objective:</h2>
    <div class="objective">
      <p class="objective-text">Sed ut perspiciatis unde omnis natus error sit voluptatem</p>
      <div class="objective-meta">
        <svg width="10" height="16" viewBox="0 0 10 16" fill="none" stroke="#9a9a9a" stroke-width="1.5"><path d="M2 2l6 6-6 6"/></svg>
        <span class="progress-label">3/5</span>
        <div class="progress"><div class="progress-fill"></div></div>
      </div>
    </div>
    <div class="objective">
      <p class="objective-text">Sed ut perspiciatis unde omnis natus error sit voluptatem</p>
      <div class="objective-meta">
        <svg width="10" height="16" viewBox="0 0 10 16" fill="none" stroke="#9a9a9a" stroke-width="1.5"><path d="M2 2l6 6-6 6"/></svg>
        <span class="progress-label">3/5</span>
        <div class="progress"><div class="progress-fill"></div></div>
      </div>
    </div>
    <div class="objective">
      <p class="objective-text">Sed ut perspiciatis unde omnis natus error sit voluptatem</p>
      <div class="objective-meta">
        <svg width="10" height="16" viewBox="0 0 10 16" fill="none" stroke="#9a9a9a" stroke-width="1.5"><path d="M2 2l6 6-6 6"/></svg>
        <span class="progress-label">3/5</span>
        <div class="progress"><div class="progress-fill"></div></div>
      </div>
    </div>
    <div class="objective">
      <p class="objective-text">Sed ut perspiciatis unde omnis natus error sit voluptatem</p>
      <div class="objective-meta">
        <svg width="10" height="16" viewBox="0 0 10 16" fill="none" stroke="#9a9a9a" stroke-width="1.5"><path d="M2 2l6 6-6 6"/></svg>
        <span class="progress-label">3/5</span>
        <div class="progress"><div class="progress-fill"></div></div>
      </div>
    </div>
    <div class="objective">
      <p class="objective-text">Sed ut perspiciatis unde omnis natus error sit voluptatem</p>
      <div class="objective-meta">
        <svg width="10" height="16" viewBox="0 0 10 16" fill="none" stroke="#9a9a9a" stroke-width="1.5"><path d="M2 2l6 6-6 6"/></svg>
        <span class="progress-label">3/5</span>
        <div class="progress"><div class="progress-fill"></div></div>
      </div>
    </div>
  </section>

  <nav class="tab-bar">
    <div class="tab">
      <svg viewBox="0 0 34 34" fill="none" stroke="#555" stroke-width="1.6"><path d="M4 17 17 5l13 12M8 14v15h18V14M14 29v-9h6v9"/></svg>
      <span>Home</span>
    </div>
    <div class="tab active">
      <svg viewBox="0 0 34 34" fill="none" stroke="#2f5f8f" stroke-width="1.8"><circle cx="17" cy="17" r="14" stroke-dasharray="14 5"/><circle cx="17" cy="17" r="8"/></svg>
      <span>Obejectives</span>
    </div>
    <div class="tab">
      <svg viewBox="0 0 34 34" fill="none" stroke="#555" stroke-width="1.6"><rect x="3" y="6" width="28" height="22" rx="2"/><path d="M7 11h10v7H7zM20 11h7M20 15h7M20 19h7M7 23h20"/></svg>
      <span>News</span>
    </div>
    <div class="tab">
      <svg viewBox="0 0 34 34" fill="none" stroke="#555" stroke-width="1.6"><path d="M22 10V5H4v24h18v-5M14 17h17M26 12l5 5-5 5"/></svg>
      <span>Logout</span>
    </div>
  </nav>
</main>
</body>
</html>
```